Business Card Design Project

I need a business card designed from scratch. I have an existing logo that I can upload in Illustrator for modification or redesign.

The Company is called Query Lanterns http://querylanterns.com.au and we provide Search Engine Optimization services to Australian businesses. The current logo signifies an increase in visitors, profits etc...

There are no restrictions as to the redesign - colours, style etc are all open to change.

Cards will be full colour and one sided printed at http://www.cardmoxel.com.au so check their requirements for file format and sizes etc.

I will expect all original files upon completion of project.

Target Market(s)

Any business with a web site looking to improve their search engine rankings

Industry/Entity Type

Business

Requirements
Must have
• I like modern, sleek designs. Clean, not fussy, uncluttered.

```html
<!DOCTYPE html>
<html lang="en">
<head>
<meta charset="utf-8">
<title>Query Lanterns – Business Card</title>
<link rel="stylesheet" href="https://fonts.googleapis.com/css2?family=Open+Sans:wght@400;600;700;800&display=swap">
<style>
  :root {
    --brand-blue: #1a72b8;
    --brand-yellow: #f5c400;
    --ink: #3a3a3a;
    --card-white: #ffffff;
    --backdrop: #ece9e4;
    --gold-start: #f4b10f;
    --gold-mid: #f5cf00;
    --gold-end: #f1e04a;
  }
  * { box-sizing: border-box; margin: 0; padding: 0; }
  html, body {
    width: 1200px; height: 460px; overflow: hidden;
    background: var(--backdrop);
    font-family: "Open Sans", Arial, sans-serif;
  }
  .stage { position: relative; width: 1200px; height: 460px; }
  .card {
    position: absolute; top: 74px;
    width: 541px; height: 310px;
    border-radius: 14px;
    box-shadow: 0 3px 8px rgba(0,0,0,0.25);
    overflow: hidden;
  }
  .card--front { left: 36px; background: var(--card-white); }
  .card--back {
    left: 624px;
    background: linear-gradient(90deg, var(--gold-start) 0%, var(--gold-mid) 55%, var(--gold-end) 100%);
  }

  /* Front */
  .brand {
    position: absolute; left: 42px; top: 62px;
    display: flex; align-items: center; gap: 10px;
  }
  .brand__dot {
    width: 16px; height: 16px; border-radius: 50%;
    background: var(--brand-yellow);
  }
  .brand__name {
    font-weight: 800; font-size: 31px; line-height: 1;
    color: var(--brand-blue); letter-spacing: -0.5px;
  }
  .name-band {
    position: absolute; left: 0; top: 170px;
    width: 362px; height: 29px;
    background: var(--brand-blue);
    clip-path: polygon(0 0, 100% 0, 97% 100%, 0 100%);
    display: flex; align-items: center;
    padding-left: 38px; color: #fff;
  }
  .name-band__name { font-weight: 700; font-size: 16px; }
  .name-band__title { font-weight: 400; font-size: 13px; margin-left: 5px; }

  .contact {
    position: absolute; left: 36px; top: 214px;
    font-size: 13px; line-height: 19px; color: var(--ink);
  }
  .contact__address { position: absolute; left: 0; top: 0; width: 180px; }
  .contact__phones { position: absolute; left: 170px; top: 0; width: 150px; }
  .contact__online { position: absolute; left: 0; top: 42px; width: 300px; }
  .contact__row { display: flex; align-items: center; gap: 6px; white-space: nowrap; }
  .contact__row svg { width: 10px; height: 10px; flex: none; fill: var(--brand-blue); }

  /* Back */
  .back-brand {
    position: absolute; left: 0; right: 0; top: 110px;
    text-align: center;
    font-weight: 800; font-size: 34px; color: #fff; letter-spacing: -0.5px;
  }
  .back-url {
    position: absolute; left: 0; right: 0; top: 222px;
    text-align: center;
    font-size: 13px; color: #fff; letter-spacing: 1.5px;
  }
</style>
</head>
<body>
<div class="stage">
  <section class="card card--front" aria-label="Business card front">
    <div class="brand">
      <span class="brand__dot"></span>
      <span class="brand__name">Query Lanterns</span>
    </div>

    <div class="name-band">
      <span class="name-band__name">Your Name</span>
      <span class="name-band__title">Title</span>
    </div>

    <div class="contact">
      <div class="contact__address">
        <div>00Floor Street, City Name</div>
        <div>State Name, Contry Name</div>
      </div>
      <div class="contact__phones">
        <div class="contact__row">
          <svg viewBox="0 0 10 10" aria-hidden="true"><path d="M2 1 L4 3 L3 4 Q4 6 6 7 L7 6 L9 8 L8 9 Q4 9 1 5 Q1 2 2 1 Z"/></svg>
          <span>098 765 4321</span>
        </div>
        <div class="contact__row">
          <svg viewBox="0 0 10 10" aria-hidden="true"><rect x="2.5" y="0.5" width="5" height="9" rx="1"/><rect x="3.5" y="1.8" width="3" height="5" fill="#fff"/></svg>
          <span>098 765 4321</span>
        </div>
      </div>
      <div class="contact__online">
        <div class="contact__row">
          <svg viewBox="0 0 10 10" aria-hidden="true"><rect x="0.5" y="2" width="9" height="6.5" rx="0.8"/><path d="M1 2.6 L5 5.8 L9 2.6" stroke="#fff" stroke-width="0.9" fill="none"/></svg>
          <span>enquiry@querylanterns.com.au</span>
        </div>
        <div class="contact__row">
          <svg viewBox="0 0 10 10" aria-hidden="true"><circle cx="5" cy="5" r="4.5"/><path d="M0.8 5 H9.2 M5 0.6 Q2.5 5 5 9.4 M5 0.6 Q7.5 5 5 9.4" stroke="#fff" stroke-width="0.7" fill="none"/></svg>
          <span>www.querylanterns.com.au</span>
        </div>
      </div>
    </div>
  </section>

  <section class="card card--back" aria-label="Business card back">
    <div class="back-brand">Query Lanterns</div>
    <div class="back-url">www.querylanterns.com.au</div>
  </section>
</div>
</body>
</html>
```